Plumbing company needs Business Card Design

Hi I need business card design based on logo which I uploaded. Its plumbing and heating company called Kranex Usługi Hydrauliczno-Gazowe. I want to see on my card motto of my company which is "...od wymiany uszczelki po wymiane łazienki.", my phone number, name, and website: 612478390, Marek Olejnik, info@kranex-inst.org, www.kranex-inst.org
I want to see logos of companys which I'm approved installer (Termova) (Le Valmont) (Korvo) (Plumox).
I want new creative look of business card. I like rounded corners.
Any questions please send message.
Thanks for intrest.
Industry/Entity Type
Business
Contact Information for Business Card
Marek Olejnik
612 478 390
info@kranex-inst.org
www.kranex-inst.org
...od wymiany uszczelki po wymiane łazienki.

```html
<!DOCTYPE html>
<html lang="pl">
<head>
<meta charset="utf-8">
<title>Kranex – wizytówka</title>
<link rel="stylesheet" href="https://fonts.googleapis.com/css2?family=Archivo+Black&family=Oswald:wght@400&display=swap">
<style>
  :root{
    --bg:#e8e3da;
    --red:#e8202c;
    --blue:#2f5aa8;
    --navy:#1d3f8f;
    --yellow:#fff23a;
    --yellow-soft:#fffbb8;
    --white:#ffffff;
    --ink:#1b1b1b;
  }
  *{box-sizing:border-box;margin:0;padding:0}
  html,body{width:1200px;height:858px;overflow:hidden;background:var(--bg)}
  .stage{position:relative;width:1200px;height:858px}
  .card{position:absolute;top:149px;width:340px;height:560px;border-radius:26px;overflow:hidden;
        box-shadow:0 6px 18px rgba(0,0,0,.18)}
  .card-front{left:170px;background:var(--white)}
  .card-back{left:690px;background:radial-gradient(ellipse at 45% 45%,var(--yellow-soft) 0%,var(--yellow) 65%)}
  .card-shape{position:absolute;inset:0;width:100%;height:100%}
  .front-content{position:absolute;inset:0;padding:52px 30px 0 30px;font-family:"Archivo Black",sans-serif}
  .brand-name{font-size:42px;color:var(--red);line-height:1}
  .brand-tagline{font-family:"Oswald",sans-serif;font-size:17px;color:var(--blue);margin-top:6px}
  .motto{font-size:11px;color:var(--navy);margin-top:8px}
  .person{font-size:26px;color:var(--blue);margin-top:24px}
  .phone{font-size:28px;color:var(--red);margin-top:22px}
  .email{font-size:19px;color:var(--red);margin-top:2px}
  .partners{margin-top:26px;display:flex;flex-wrap:wrap;gap:10px 22px;padding-left:20px;width:250px}
  .partner{font-size:17px;color:var(--ink);line-height:1}
  .website{font-size:22px;color:var(--red);margin-top:26px;padding-left:10px}
  .back-content{position:absolute;left:50%;top:46%;width:520px;transform:translate(-50%,-50%) rotate(90deg);text-align:center}
  .back-name{font-family:"Archivo Black",sans-serif;font-size:100px;color:var(--red);line-height:1}
  .back-tagline{font-family:"Oswald",sans-serif;font-size:32px;color:var(--blue);margin-top:6px}
</style>
</head>
<body>
<main class="stage">
  <section class="card card-front" aria-label="Przód wizytówki">
    <svg class="card-shape" viewBox="0 0 340 560" aria-hidden="true">
      <path d="M205 0 H340 V270 C336 150 290 55 205 0 Z" fill="var(--red)"/>
      <path d="M196 0 C282 52 328 148 334 270" fill="none" stroke="var(--blue)" stroke-width="3"/>
      <path d="M0 300 C6 420 60 505 150 560 H0 Z" fill="var(--red)"/>
      <path d="M8 300 C16 415 70 502 162 560" fill="none" stroke="var(--blue)" stroke-width="3"/>
    </svg>
    <div class="front-content">
      <p class="brand-name">Kranex</p>
      <p class="brand-tagline">Usługi Hydrauliczno-Gazowe</p>
      <p class="motto">...od wymiany uszczelki po wymiane łazienki.</p>
      <p class="person">Marek Olejnik</p>
      <p class="phone">612 478 390</p>
      <p class="email">info@kranex-inst.org</p>
      <div class="partners">
        <span class="partner">Le Valmont</span>
        <span class="partner">Termova</span>
        <span class="partner">Korvo</span>
        <span class="partner">Plumox</span>
      </div>
      <p class="website">www.kranex-inst.org</p>
    </div>
  </section>

  <section class="card card-back" aria-label="Tył wizytówki">
    <svg class="card-shape" viewBox="0 0 340 560" aria-hidden="true">
      <path d="M0 470 C110 520 230 520 340 440 V560 H0 Z" fill="var(--red)"/>
      <path d="M0 462 C110 512 230 512 340 432" fill="none" stroke="var(--blue)" stroke-width="3"/>
    </svg>
    <div class="back-content">
      <p class="back-name">Kranex</p>
      <p class="back-tagline">Usługi Hydrauliczno-Gazowe</p>
    </div>
  </section>
</main>
</body>
</html>
```